Dean Hartwell realestate

We want something complete different to our website now and something that will stand out this is our website http://deanhartwellrealestate.com/

our company website for my boss is www.gordonvale.com

please note this website is being made for dean hartwell not gordon vale

something similar to our company website but has to be in the branding of dean hartwell realestate

```html
<!DOCTYPE html>
<html lang="en">
<head>
<meta charset="utf-8">
<title>Dean Hartwell Property</title>
<link rel="stylesheet" href="https://fonts.googleapis.com/css2?family=Oswald:wght@500;600&family=Roboto:wght@400;500;700&family=Open+Sans:wght@400;600&family=Poppins:wght@400;500;600&display=swap">
<style>
:root{
  --orange:#f15a22;
  --orange-soft:#f47a45;
  --ink:#1d1d1d;
  --text:#555;
  --muted:#777;
  --navy:#1f3c6b;
  --panel:#f1f1f1;
  --line:#d9d9d9;
  --sky-blue:#eaf3fb;
  --footer:#1b1b1b;
  --white:#fff;
}
*{box-sizing:border-box;margin:0;padding:0}
html,body{width:1200px;height:3774px;overflow:hidden}
body{position:relative;font-family:"Open Sans",sans-serif;color:var(--text);background:var(--white)}
.abs{position:absolute}

/* Hero */
.hero{position:absolute;left:0;top:0;width:1200px;height:606px;background:linear-gradient(180deg,#3a3f8c 0%,#5a4f8f 40%,#2c3550 75%,#2a3323 100%)}
.hero-photo{position:absolute;inset:0;background:radial-gradient(ellipse 520px 300px at 600px 380px,rgba(232,190,130,.55),rgba(0,0,0,0) 70%),linear-gradient(180deg,rgba(0,0,0,0) 55%,rgba(30,40,20,.7) 100%)}
.brand{position:absolute;left:131px;top:38px;font-family:"Oswald",sans-serif;font-weight:600;font-size:30px;color:var(--white);letter-spacing:.5px}
.main-nav{position:absolute;left:478px;top:38px;display:flex;gap:6px;align-items:center}
.main-nav a{font-family:"Oswald",sans-serif;font-weight:500;font-size:16px;color:var(--white);text-decoration:none;padding:6px 14px;letter-spacing:.4px}
.main-nav a.active{border:2px solid var(--white);border-radius:3px}
.nav-social{position:absolute;left:1004px;top:42px;display:flex;gap:10px}
.nav-social span{width:26px;height:26px;border-radius:50%;background:var(--white)}
.slider-dots{position:absolute;left:1114px;top:180px;display:flex;flex-direction:column;gap:8px}
.slider-dots span{width:14px;height:14px;border-radius:50%;border:2px solid var(--white)}
.slider-dots span.on{border-color:var(--orange)}
.hero-card{position:absolute;left:410px;top:297px;width:383px;height:219px;border:3px solid var(--white);background:rgba(255,255,255,.82);text-align:center;padding-top:34px}
.hero-card h1{font-family:"Oswald",sans-serif;font-weight:600;font-size:38px;line-height:44px;color:#2a2a2a;letter-spacing:.5px}
.btn-orange{display:inline-block;background:var(--orange);color:var(--white);font-family:"Roboto",sans-serif;font-weight:700;text-transform:uppercase}
.hero-card .btn-orange{margin-top:16px;font-size:16px;padding:10px 18px}

/* Listings */
.section-title{font-family:"Roboto",sans-serif;font-weight:700;color:var(--ink);text-align:center}
.sale-title{position:absolute;left:0;top:666px;width:1200px;font-size:32px}
.pill-row{position:absolute;left:0;top:728px;width:1200px;display:flex;justify-content:center;gap:22px}
.pill{border:2px solid #222;border-radius:22px;padding:7px 22px;font-family:"Roboto",sans-serif;font-size:15px;color:#222}
.listing{position:absolute;left:131px;width:662px;height:200px}
.listing.featured{background:var(--white);box-shadow:0 2px 10px rgba(0,0,0,.15)}
.listing-photo{position:absolute;left:0;top:0;width:284px;height:200px;overflow:hidden}
.sold{position:absolute;left:-36px;top:16px;width:130px;transform:rotate(-45deg);background:var(--orange);color:var(--white);text-align:center;font-family:"Roboto",sans-serif;font-weight:700;font-size:13px;padding:4px 0}
.listing-body{position:absolute;left:312px;top:18px;width:340px}
.listing-body h3{font-family:"Roboto",sans-serif;font-weight:500;font-size:19px;color:var(--ink);text-transform:uppercase}
.price{margin-top:10px;font-family:"Roboto",sans-serif;font-weight:700;font-size:15px;color:var(--ink)}
.price b{color:var(--orange);font-weight:500}
.address{margin-top:9px;font-size:13px;color:var(--text);display:flex;align-items:center;gap:8px}
.blurb{margin-top:8px;font-size:12.5px;line-height:19px;color:var(--text)}
.features{margin-top:12px;display:flex;gap:22px;align-items:center;font-size:13px;color:var(--text)}
.features .type{color:var(--navy);font-size:15px;margin-right:6px}
.features span{display:flex;align-items:center;gap:8px}

.search-box{position:absolute;left:825px;top:825px;width:242px}
.box-head{background:var(--orange);color:var(--white);font-family:"Roboto",sans-serif;font-weight:700;font-size:18px;text-align:center;padding:13px 0}
.search-form{background:var(--panel);padding:16px 14px 20px}
.radio-row{display:flex;gap:10px;align-items:center;font-size:12px;color:#444;margin-bottom:18px}
.radio-row i{width:11px;height:11px;border-radius:50%;border:1px solid #888;display:inline-block;margin-right:4px;vertical-align:-1px}
.select{background:var(--white);border:1px solid var(--line);height:36px;margin-bottom:12px;font-size:11px;color:#888;padding:10px 10px;position:relative}
.select:after{content:"";position:absolute;right:10px;top:15px;border:4px solid transparent;border-top-color:#555}
.search-form .btn-orange{display:block;text-align:center;font-size:14px;padding:11px 0;margin-top:14px}
.refine-box{position:absolute;left:825px;top:1283px;width:242px;height:370px;background:var(--panel);border:1px solid var(--line)}
.refine-box h4{background:var(--white);font-family:"Roboto",sans-serif;font-weight:500;font-size:16px;color:#333;text-align:center;padding:13px 0;border-bottom:1px solid var(--line)}
.refine-box ul{list-style:none;padding:10px 16px}
.refine-box li{font-size:12px;color:#444;line-height:26.5px}
.upcoming{position:absolute;left:825px;top:1675px;width:242px;text-align:center;font-size:14px;padding:11px 0}

/* Welcome */
.welcome{position:absolute;left:0;top:1819px;width:1200px;height:503px;background:linear-gradient(135deg,#f4f9fe,var(--sky-blue))}
.video-frame{position:absolute;left:133px;top:106px;width:418px;height:297px;background:var(--white);padding:5px;box-shadow:0 1px 4px rgba(0,0,0,.15)}
.video-photo{width:100%;height:100%;background:linear-gradient(180deg,#8aa07a 0%,#6f7f55 45%,#4d7a2c 75%,#3f6b26 100%);position:relative}
.play{position:absolute;left:180px;top:120px;width:52px;height:40px;background:#e23a2e;border-radius:8px}
.play:after{content:"";position:absolute;left:20px;top:11px;border-left:16px solid var(--white);border-top:9px solid transparent;border-bottom:9px solid transparent}
.welcome-copy{position:absolute;left:596px;top:112px;width:470px}
.welcome-copy h2{font-family:"Roboto",sans-serif;font-weight:700;font-size:29px;line-height:37px;color:var(--ink);text-transform:uppercase}
.welcome-copy p{margin-top:18px;font-size:13px;line-height:25px;color:#444}
.btn-outline{display:inline-block;margin-top:14px;border:2px solid #222;padding:6px 12px;font-family:"Roboto",sans-serif;font-weight:500;font-size:14px;color:#222}

/* Testimonials */
.clients{position:absolute;left:0;top:2322px;width:1200px;height:546px;background:linear-gradient(180deg,#e4672a 0%,#d8571f 50%,#c74d1c 100%)}
.clients-title{position:absolute;left:0;top:84px;width:1200px;text-align:center;font-family:"Roboto",sans-serif;font-weight:500;font-size:31px;color:var(--white)}
.testimonial{position:absolute;top:227px;height:161px;background:var(--white);border-radius:10px;box-shadow:0 3px 10px rgba(0,0,0,.2);padding:50px 24px 0;text-align:center;font-size:12px;line-height:21px;font-style:italic;color:#444}
.testimonial q{quotes:none}
.testimonial b{font-style:normal;font-size:18px;font-weight:700;margin-right:4px;color:#222}
.avatar{position:absolute;top:-46px;width:86px;height:86px;border-radius:50%;border:4px solid var(--white);background:linear-gradient(160deg,#c9b39a,#7a5f4a)}
.client-name{position:absolute;top:420px;text-align:center;font-family:"Roboto",sans-serif;font-size:15px;line-height:20px;color:var(--white)}

/* Selling */
.sell-title{position:absolute;left:0;top:2946px;width:1200px;font-size:31px}
.sell-sub{position:absolute;left:0;top:3000px;width:1200px;text-align:center;font-family:"Roboto",sans-serif;font-size:19px;color:#333}
.sell-actions{position:absolute;left:0;top:3050px;width:1200px;display:flex;justify-content:center;gap:18px}
.sell-actions .pill{font-weight:500;font-size:15px;text-transform:uppercase}
.sell-actions .pill.alt{border-color:var(--orange);color:var(--orange)}
.skyline{position:absolute;left:50px;top:3118px;width:1100px;height:160px;background:linear-gradient(180deg,rgba(200,200,200,0) 0%,#e6e6e6 60%,#d4d4d4 100%)}

/* Footer */
.site-footer{position:absolute;left:0;top:3235px;width:1200px;height:539px}
.footer-curve{position:absolute;left:0;top:0}
.footer-body{position:absolute;left:0;top:60px;width:1200px;height:479px;background:var(--footer);font-family:"Poppins",sans-serif}
.footer-col{position:absolute;top:92px}
.footer-col h5{font-weight:600;font-size:24px;color:var(--white)}
.footer-col h5 em{font-style:normal;color:var(--orange)}
.quick-links{list-style:none;margin-top:22px}
.quick-links li{font-size:13px;color:#ddd;line-height:24.5px}
.quick-links li:before{content:"›";color:#ddd;margin-right:12px}
.foot-social{display:flex;gap:6px;margin-top:10px}
.foot-social span{width:20px;height:20px;border-radius:50%;border:1px solid #bbb}
.contact-list{list-style:none;margin-top:26px}
.contact-list li{display:flex;gap:12px;font-size:12px;line-height:19px;color:#ddd;margin-bottom:14px}
.contact-list svg{flex:none;margin-top:2px}
.quote-lead{margin-top:22px;font-size:14px;color:#ddd}
.quote-form{display:grid;grid-template-columns:211px 209px;gap:10px 15px;margin-top:26px}
.field{height:38px;border:1px solid #777;font-size:11px;color:#ccc;padding:11px 12px}
.quote-form .btn-orange{height:38px;font-size:15px;text-align:center;padding-top:9px;font-family:"Poppins",sans-serif;font-weight:600}
.copyright{position:absolute;left:0;top:424px;width:1200px;text-align:center;font-size:12px;color:#ccc}
</style>
</head>
<body>

<header class="hero">
  <div class="hero-photo" role="img" aria-label="Photo of a two-storey family home with lit windows at dusk"></div>
  <div class="brand">DEAN HARTWELL PROPERTY</div>
  <nav class="main-nav">
    <a class="active" href="#">HOME</a><a href="#">FOR SALE</a><a href="#">AGENTS</a><a href="#">BOOK APPRAISAL</a><a href="#">CONTACT</a>
  </nav>
  <div class="nav-social"><span></span><span></span></div>
  <div class="slider-dots"><span></span><span></span><span class="on"></span><span></span></div>
  <div class="hero-card">
    <h1>DEAN HARTWELL<br>PROPERTY</h1>
    <span class="btn-orange">Book Appraisal</span>
  </div>
</header>

<h2 class="section-title sale-title">PROPERTIES FOR SALE</h2>
<div class="pill-row"><span class="pill">View Off the Plan Projects</span><span class="pill">Receive Property Alerts</span></div>

<article class="listing" style="top:825px">
  <div class="listing-photo" role="img" aria-label="Photo of a brick single-storey home with garage" style="background:linear-gradient(180deg,#8fc1ea 0%,#b9d6ec 40%,#b57a55 60%,#8b8b84 100%)"></div>
  <div class="listing-body">
    <h3>Modern home in top end Rivervale!</h3>
    <p class="price">From <b>$549,000 - $589,000</b></p>
    <p class="address"><svg width="10" height="13" viewBox="0 0 10 13"><path d="M5 0a5 5 0 0 0-5 5c0 3.5 5 8 5 8s5-4.5 5-8a5 5 0 0 0-5-5zm0 7a2 2 0 1 1 0-4 2 2 0 0 1 0 4z" fill="#555"/></svg>14 Marlow Street, Eastbrook, WA 6103</p>
    <p class="blurb">Lorem ipsum dolor sit amet, consectetur adipiscing elit, sed do eiusmod tempor incididunt ut labore et dolore magna</p>
    <div class="features"><span class="type">House</span><span>🛏 3</span><span>🛁 2</span><span>🚗 2</span></div>
  </div>
</article>

<article class="listing featured" style="top:1057px">
  <div class="listing-photo" role="img" aria-label="Photo of a modern home front gate lit at dusk" style="background:linear-gradient(180deg,#6a6f7a 0%,#4d4a48 50%,#2e2a28 100%)"><div class="sold">SOLD</div></div>
  <div class="listing-body">
    <h3>Quis autem vel eum iure repr</h3>
    <p class="price">From <b>$549,000 - $589,000</b></p>
    <p class="address"><svg width="10" height="13" viewBox="0 0 10 13"><path d="M5 0a5 5 0 0 0-5 5c0 3.5 5 8 5 8s5-4.5 5-8a5 5 0 0 0-5-5zm0 7a2 2 0 1 1 0-4 2 2 0 0 1 0 4z" fill="#555"/></svg>14 Marlow Street, Eastbrook, WA 6103</p>
    <p class="blurb">Lorem ipsum dolor sit amet, consectetur adipiscing elit, sed do eiusmod tempor incididunt ut labore et dolore magna</p>
    <div class="features"><span class="type">House</span><span>🛏 3</span><span>🛁 2</span><span>🚗 2</span></div>
  </div>
</article>

<article class="listing" style="top:1288px">
  <div class="listing-photo" role="img" aria-label="Photo of a white two-storey townhouse" style="background:linear-gradient(180deg,#5d8fc8 0%,#a9c7e6 35%,#e9e9e7 60%,#9a9a98 100%)"></div>
  <div class="listing-body">
    <h3>Lucky last dont miss out!</h3>
    <p class="price">From <b>$549,000 - $589,000</b></p>
    <p class="address"><svg width="10" height="13" viewBox="0 0 10 13"><path d="M5 0a5 5 0 0 0-5 5c0 3.5 5 8 5 8s5-4.5 5-8a5 5 0 0 0-5-5zm0 7a2 2 0 1 1 0-4 2 2 0 0 1 0 4z" fill="#555"/></svg>14 Marlow Street, Eastbrook, WA 6103</p>
    <p class="blurb">Lorem ipsum dolor sit amet, consectetur adipiscing elit, sed do eiusmod tempor incididunt ut labore et dolore magna</p>
    <div class="features"><span class="type">House</span><span>🛏 3</span><span>🛁 2</span><span>🚗 2</span></div>
  </div>
</article>

<article class="listing" style="top:1515px">
  <div class="listing-photo" role="img" aria-label="Photo of a grey-roofed modern home" style="background:linear-gradient(180deg,#7fb4e0 0%,#bcd6ea 35%,#c9ccd0 60%,#8d9196 100%)"></div>
  <div class="listing-body">
    <h3>Modern home in top end Rivervale!</h3>
    <p class="price">From <b>$549,000 - $589,000</b></p>
    <p class="address"><svg width="10" height="13" viewBox="0 0 10 13"><path d="M5 0a5 5 0 0 0-5 5c0 3.5 5 8 5 8s5-4.5 5-8a5 5 0 0 0-5-5zm0 7a2 2 0 1 1 0-4 2 2 0 0 1 0 4z" fill="#555"/></svg>14 Marlow Street, Eastbrook, WA 6103</p>
    <p class="blurb">Lorem ipsum dolor sit amet, consectetur adipiscing elit, sed do eiusmod tempor incididunt ut labore et dolore magna</p>
    <div class="features"><span class="type">House</span><span>🛏 3</span><span>🛁 2</span><span>🚗 2</span></div>
  </div>
</article>

<aside class="search-box">
  <div class="box-head">PROPERTY SEARCH</div>
  <div class="search-form">
    <div class="radio-row">BUY OR RENT : <span><i></i>BUY</span><span><i></i>RENT</span></div>
    <div class="select">Type :</div>
    <div class="select">Bedrooms :</div>
    <div class="select">Min Price :</div>
    <div class="select">Max Price :</div>
    <div class="select">Offices :</div>
    <span class="btn-orange">Property Search</span>
  </div>
</aside>
<aside class="refine-box">
  <h4>REFINE BY LOCATION</h4>
  <ul>
    <li>Belmont (5)</li><li>Carlisle (4)</li><li>Cloverdale (3)</li><li>East Victoria Park (3)</li><li>High Wycombe (1)</li><li>Kewdale (12)</li><li>Lathlain (2)</li><li>Orange Grove (1)</li><li>Redcliffe (2)</li><li>Rivervale (11)</li><li>St James (4)</li>
  </ul>
</aside>
<span class="btn-orange upcoming">Upcoming Home Opens</span>

<section class="welcome">
  <div class="video-frame"><div class="video-photo" role="img" aria-label="Video still of the agent standing in a park"><span class="play"></span></div></div>
  <div class="welcome-copy">
    <h2>Welcome to<br>Dean Hartwell Property</h2>
    <p>Sed ut perspiciatis unde omnis iste natus error sit voluptatem accusantium remque laudantium, totam rem aperiam, eaque ipsa quae ab illo inventore veritatis et quasi architecto beatae vitae dicta sunt explicabo. Nemo enim ipsam voluptatem quia voluptas sit aspernatur aut odit aut fugit, sed quia consequuntur magni dolores eos qui ratione voluptatem sequi nesciunt. Neque porro quisquam</p>
    <span class="btn-outline">MORE VIDEOS</span>
  </div>
</section>

<section class="clients" role="img" aria-label="Orange-tinted background photo of a family outside a house">
  <h2 class="clients-title">WHAT OUR CLIENTS THINK</h2>
  <div class="testimonial" style="left:151px;width:302px"><div class="avatar" style="left:108px"></div><b>“</b>We bought our first home through Dean and the process was easy and very straight forward. We felt confident buying our first home and extremely supported.</div>
  <div class="testimonial" style="left:463px;width:274px"><div class="avatar" style="left:94px"></div><b>“</b>I found Dean to be different from most agents, in that he listened, and set a marketing program to suit the special features of our property. Eager to do anything</div>
  <div class="testimonial" style="left:772px;width:275px"><div class="avatar" style="left:94px"></div><b>“</b>Dean is very talented and highly ethical person who provides a high standard of customer service both during the transaction and after.</div>
  <div class="client-name" style="left:151px;width:302px">– Isabela &amp; Javier<br>Kewdale, 6105</div>
  <div class="client-name" style="left:463px;width:274px">– Ian<br>Lathlain, 6100</div>
  <div class="client-name" style="left:772px;width:275px">– Harry<br>Rivervale, 6103</div>
</section>

<h2 class="section-title sell-title">INTERESTED IN SELLING YOUR PROPERTY?</h2>
<p class="sell-sub">Get in touch, we'll walk you through the rest</p>
<div class="sell-actions"><span class="pill">Request a Market Appraisal</span><span class="pill alt">Contact Us</span></div>
<div class="skyline" role="img" aria-label="Line illustration of a city skyline with houses, trees and clouds"></div>

<footer class="site-footer">
  <svg class="footer-curve" width="1200" height="70" viewBox="0 0 1200 70">
    <path d="M0 20 Q600 -20 1200 20 L1200 70 L0 70 Z" fill="#1b1b1b"/>
    <path d="M60 30 Q600 -6 1140 30" fill="none" stroke="#f15a22" stroke-width="4"/>
  </svg>
  <div class="footer-body">
    <div class="footer-col" style="left:131px">
      <h5>Quick <em>Links</em></h5>
      <ul class="quick-links"><li>Home</li><li>For Sale</li><li>Agents</li><li>Book Appraisal</li><li>Contact</li></ul>
      <div class="foot-social"><span></span><span></span><span></span><span></span></div>
    </div>
    <div class="footer-col" style="left:325px">
      <h5>Contact <em>Us</em></h5>
      <ul class="contact-list">
        <li><svg width="11" height="14" viewBox="0 0 10 13"><path d="M5 0a5 5 0 0 0-5 5c0 3.5 5 8 5 8s5-4.5 5-8a5 5 0 0 0-5-5zm0 7a2 2 0 1 1 0-4 2 2 0 0 1 0 4z" fill="#fff"/></svg><span>Dean Hartwell Property<br>Suite 12, 40 Larkspur Road,<br>Eastbrook, WA 6103 Australia</span></li>
        <li><svg width="12" height="12" viewBox="0 0 12 12"><path d="M2.4 0 4.5 2.6 3.4 4.3c.8 1.7 2.2 3.1 3.9 3.9l1.7-1.1L12 9.6 10.2 12C4.6 12 0 7.4 0 1.8Z" fill="#fff"/></svg><span>Phone 0400 512 378<br>Fax 0500 118 274</span></li>
        <li><svg width="13" height="10" viewBox="0 0 13 10"><rect width="13" height="10" rx="1" fill="#fff"/><path d="M0 1 6.5 6 13 1" fill="none" stroke="#1b1b1b" stroke-width="1.2"/></svg><span>Email: info@deanhartwellrealestate.com</span></li>
      </ul>
    </div>
    <div class="footer-col" style="left:632px">
      <h5>Get a <em>Quote</em></h5>
      <p class="quote-lead">Alternatively You Can Fill In The Following Contact Form:</p>
      <div class="quote-form">
        <div class="field">Name</div><div class="field">E - Mail</div>
        <div class="field">Phone No</div><span class="btn-orange">SUBMIT</span>
      </div>
    </div>
    <p class="copyright">© 2018 Dean Hartwell Property. All Rights Reserved.</p>
  </div>
</footer>

</body>
</html>
```